Two Wine Labels, One Red One White

We are looking to create a brand image for our wines. There are two requirements by law that we need, however beyond that, the creativity comes from the designer. Required are:
On The Red Label, Alcohol 14.1White Label Alcohol 12.5, The Size, 750ML
SO One label for the red wine with alcohol at 14.1 in a 750 ML Bottle, and one Label for white with alcohol at 12.5 in a 750 ML bottle.

Hi All:
I have some more clarity to assist in the design work.
The Brand Name of the wine is Valquine for both the red and the white
The name should appear as Valquine with the Brackets around phonetical as seen here
[val-keen] Both the word and the phonetical spelling should appear.
and can be seen on lexiquarry.com The Brand Name text can be black
Label should be very light grey, I am trying to capture a Stone grey or texture from stone, although, NOT Marble.
The Red Label, The word "Red" should be in red
The White Label, The word "White" should be in White, all the original remaining elements remain as originally posted.

I look forward to hearing from you for any additional questions.
Updates

Just added a logo Not really seeing what we are trying to achieve, maybe using the logo in the design may assist

Target Market(s)

Wine Aficionados

Requirements
Must have
• Details described in Project Description above, these are required by law. The Name of the Brand will be posted shortly. For the moment if you take the project, just place red on one label and white on the other.
Nice to have
• These two wines are from California (USA), so the Sierra Nevada Mountains could be an inspiration, to outline of California or coast line, a vineyard (of course), a vine...We are in silicon valley, so there is a map of silicon valley with the Bay and ocean, something from a map could work, or let your creativity flow and not use any of these concepts.
Should not have
• I do not not care for decorative fonts, however all else is open

```html
<!DOCTYPE html>
<html lang="en">
<head>
<meta charset="utf-8">
<title>Valquine Wine Labels</title>
<link rel="stylesheet" href="https://fonts.googleapis.com/css2?family=Questrial&family=Open+Sans:wght@300;400&display=swap">
<style>
  :root {
    --backdrop: #130006;
    --label-stone: #e8e7e3;
    --ink: #111111;
    --red-accent: #ec1c24;
    --white-accent: #d9e021;
    --band-text: #ffffff;
  }
  html, body {
    margin: 0;
    padding: 0;
    width: 1200px;
    height: 900px;
    overflow: hidden;
    background: var(--backdrop);
  }
  .canvas {
    position: relative;
    width: 1200px;
    height: 900px;
    background: var(--backdrop);
  }
  .label {
    position: absolute;
    top: 141px;
    width: 443px;
    height: 617px;
    background: var(--label-stone);
    --accent: var(--red-accent);
  }
  .label--red { left: 134px; --accent: var(--red-accent); }
  .label--white { left: 622px; --accent: var(--white-accent); }

  .label__scene-frame {
    position: absolute;
    left: 0;
    top: 33px;
    width: 100%;
    height: 242px;
    background: var(--accent);
  }
  .label__scene {
    position: absolute;
    left: 0;
    top: 19px;
    width: 100%;
    height: 204px;
    display: block;
  }
  .label__brand {
    position: absolute;
    left: 0;
    top: 305px;
    width: 100%;
    margin: 0;
    text-align: center;
    font-family: "Questrial", "Century Gothic", sans-serif;
    font-weight: 400;
    font-size: 64px;
    line-height: 1;
    color: var(--ink);
  }
  .label__phonetic {
    position: absolute;
    left: 0;
    top: 383px;
    width: 100%;
    margin: 0;
    text-align: center;
    font-family: "Questrial", "Century Gothic", sans-serif;
    font-size: 26px;
    line-height: 1;
    color: var(--accent);
  }
  .label__variety {
    position: absolute;
    left: 0;
    top: 421px;
    width: 100%;
    height: 66px;
    box-sizing: border-box;
    margin: 0;
    background: var(--accent);
    display: flex;
    justify-content: space-between;
    align-items: center;
    font-family: "Open Sans", "Helvetica Neue", sans-serif;
    font-weight: 300;
    font-size: 72px;
    line-height: 1;
    color: var(--band-text);
  }
  .label--red .label__variety { padding: 0 96px 0 98px; }
  .label--white .label__variety { padding: 0 6px 0 10px; }

  .label__facts {
    position: absolute;
    left: 0;
    top: 536px;
    width: 100%;
    margin: 0;
    text-align: center;
    font-family: "Open Sans", "Helvetica Neue", sans-serif;
    font-size: 21px;
    line-height: 34px;
    color: var(--ink);
  }
</style>
</head>
<body>
<main class="canvas">

  <article class="label label--red">
    <div class="label__scene-frame">
      <svg class="label__scene" viewBox="0 0 443 204" preserveAspectRatio="none" role="img" aria-label="Painted landscape of red mountains beside a lake under a turquoise sky">
        <defs>
          <linearGradient id="red-scene" x1="0" y1="0" x2="0" y2="1">
            <stop offset="0" stop-color="#3fd0d8"/>
            <stop offset="0.22" stop-color="#58c6cc"/>
            <stop offset="0.42" stop-color="#b8473c"/>
            <stop offset="0.62" stop-color="#cf5a43"/>
            <stop offset="0.78" stop-color="#3f8fb0"/>
            <stop offset="1" stop-color="#b84a30"/>
          </linearGradient>
        </defs>
        <rect width="443" height="204" fill="url(#red-scene)"/>
      </svg>
    </div>
    <h1 class="label__brand">Valquine</h1>
    <p class="label__phonetic">[val-keen]</p>
    <p class="label__variety" aria-label="Red"><span>R</span><span>E</span><span>D</span></p>
    <p class="label__facts">Alcohol 14.1<br>750мл.</p>
  </article>

  <article class="label label--white">
    <div class="label__scene-frame">
      <svg class="label__scene" viewBox="0 0 443 204" preserveAspectRatio="none" role="img" aria-label="Painted landscape of golden mountains beside a blue lake under a deep blue sky">
        <defs>
          <linearGradient id="white-scene" x1="0" y1="0" x2="0" y2="1">
            <stop offset="0" stop-color="#2f5fd6"/>
            <stop offset="0.24" stop-color="#4a72d0"/>
            <stop offset="0.44" stop-color="#a88f3e"/>
            <stop offset="0.62" stop-color="#d8c060"/>
            <stop offset="0.78" stop-color="#2a3fb8"/>
            <stop offset="1" stop-color="#c9aa48"/>
          </linearGradient>
        </defs>
        <rect width="443" height="204" fill="url(#white-scene)"/>
      </svg>
    </div>
    <h1 class="label__brand">Valquine</h1>
    <p class="label__phonetic">[val-keen]</p>
    <p class="label__variety" aria-label="White"><span>W</span><span>H</span><span>I</span><span>T</span><span>E</span></p>
    <p class="label__facts">Alcohol 12.5<br>750мл.</p>
  </article>

</main>
</body>
</html>
```